Business card design

I already have the logo design completed and am requiring business card design and layout utilising the logo. I require a front and back design.

We are an executive recruitment company so we are looking at full colour, high finish in a reasonably conservative structure.

Reason: will be provide ai template

Target Market(s)

Senior Management 35-60 age bracket

Industry/Entity Type

Business

Requirements
Must have
• Peter Welling
• Director
• 238 Morrow Tce, Kelvin Grove QLD 4059
• Ph: 07 3628 4190 Mob: 0418527306
• peter@voltinapartners.com.au
• www.voltinapartners.com.au
Nice to have
• Ideally full colour,
Should not have
• cheap looking

```html
<!DOCTYPE html>
<html lang="en">
<head>
<meta charset="utf-8">
<title>Voltina Partners – Business Card</title>
<link rel="stylesheet" href="https://fonts.googleapis.com/css2?family=Montserrat:wght@500;600;700&display=swap">
<style>
  :root {
    --stage: #6b6b6b;
    --card-light: #e8e8e8;
    --brand-blue: #0c4a7e;
    --text-grey: #3f3f3f;
    --rule-blue: #5b7fa6;
    --back-top: #064c80;
    --back-bottom: #03335f;
    --white: #ffffff;
  }
  * { margin: 0; padding: 0; box-sizing: border-box; }
  html, body { width: 1200px; height: 900px; overflow: hidden; }
  body {
    background: var(--stage);
    position: relative;
    font-family: "Montserrat", sans-serif;
  }
  .card {
    position: absolute;
    left: 284px;
    width: 633px;
    height: 352px;
  }
  .card--front { top: 62px; background: var(--card-light); }
  .card--back {
    top: 486px;
    background: linear-gradient(to bottom, var(--back-top) 0%, var(--back-top) 45%, var(--back-bottom) 100%);
  }
  .brand {
    position: absolute;
    display: flex;
    align-items: center;
    gap: 9px;
    white-space: nowrap;
  }
  .brand__square { flex: none; }
  .brand__name { font-weight: 700; letter-spacing: 0.3px; }
  .card--front .brand { left: 62px; top: 158px; }
  .card--front .brand__square { background: var(--brand-blue); width: 30px; height: 30px; }
  .card--front .brand__name { color: var(--brand-blue); font-size: 15px; }
  .card--back .brand { left: 50%; top: 177px; transform: translate(-50%, -50%); }
  .card--back .brand__square { background: var(--white); width: 40px; height: 40px; }
  .card--back .brand__name { color: var(--white); font-size: 25px; }
  .divider {
    position: absolute;
    left: 316px;
    top: 67px;
    width: 2px;
    height: 222px;
    background: var(--rule-blue);
  }
  .contact {
    position: absolute;
    left: 355px;
    top: 100px;
    color: var(--text-grey);
    font-weight: 700;
    font-size: 12px;
    line-height: 20px;
  }
  .contact__name {
    color: var(--brand-blue);
    font-size: 34px;
    line-height: 40px;
    font-weight: 700;
    margin-bottom: 2px;
  }
  .contact__email { font-weight: 600; font-size: 12px; }
  .contact__address { margin-top: 18px; }
  .website {
    position: absolute;
    left: 0;
    right: 0;
    top: 303px;
    text-align: center;
    font-size: 20px;
    font-weight: 600;
    letter-spacing: 1.6px;
  }
  .card--front .website { color: var(--brand-blue); }
  .card--back .website { color: var(--white); top: 302px; }
</style>
</head>
<body>
  <section class="card card--front">
    <div class="brand">
      <span class="brand__square"></span>
      <span class="brand__name">VOLTINA PARTNERS</span>
    </div>
    <div class="divider"></div>
    <div class="contact">
      <p class="contact__name">NAME</p>
      <p class="contact__phone">XXXX XXX XXX</p>
      <p class="contact__email">admin@voltinapartners.com.au</p>
      <div class="contact__address">
        <p>PO BOX XX</p>
        <p>XXXX XXXX XXXX</p>
        <p>XXXX XX</p>
      </div>
    </div>
    <p class="website">www.voltinapartners.com.au</p>
  </section>

  <section class="card card--back">
    <div class="brand">
      <span class="brand__square"></span>
      <span class="brand__name">VOLTINA PARTNERS</span>
    </div>
    <p class="website">www.voltinapartners.com.au</p>
  </section>
</body>
</html>
```